Window Treatment business needs website redesigned.

We need a revamp and refresh of our current site www.velmarix.ca
Looking to attract very high end customer. It should be a very simple design with very little text. This site will be visited by prospective homeowners, designers, builders and architects. They should feel that they are dealing with a high-end product selection, where experience, customer service and unique product offering is the focus. The content will be to highlight our services and highlight the manufacturers we sell, using a few rich photos to highlight the products. We should NOT look like we are a very large company. It should NOT have discounts/savings buttons and many menus to choose from. We offer over 15 years experience to narrow the many market options, to provide the right technical solution.
We specialize in products that are not readily available on the market and specifically motorized systems for indoors and outdoors.
Our main suppliers are Kravenholt.com, Dimbrell.com
We carry our own locally manufactured product line of roller shades.
Main product pictures should be of roller shades, outdoor bug screens, awnings and outdoor pergolas.

Reason: I understand that Christmas is coming up real short and many people are extremely busy. If you have a CREATIVE gifting you still want to submit, I look forward to your idea!

Reason: Due to holiday season, we have not had sufficient time to review to make a final decision. Thank you for your patience!

Target Market(s)

High end home owners, designers, builders, architects

Industry/Entity Type

Contractor

Coding

Coded - Design and coding required

Number of Pages Required

3 page

Font styles to use
Sans Serif

Requirements
Must have
• Landing page with full size image like homepage of zolvane.it
• Products page that highlights products with simple product shot image, description and link to manufacturer.
• On main page a scrolling of customer reviews.
• I want a very simple, eye-catching, emotional image for homepage. It does not need to include any product image.
• An image that shows technology combining/meshing with hand craftsmanship.
• Focus is on design.
• http://www.zolvane.it/en/gallery is a great layout and design.
Nice to have
• Logo shape for icons and watermark should be used.
• Look like and have simple motion effects like quorix.com or telvarin.com
Should not have
• Generic/standard looking feel like bluppet.com or mecklorwindow.ca
• No use of green as background only subtle text.
• Lots of text and pages.

```html
<!DOCTYPE html>
<html lang="en">
<head>
<meta charset="utf-8">
<title>Velmarix Window Treatment Solution</title>
<link href="https://fonts.googleapis.com/css2?family=Oswald:wght@500;600&family=Raleway:wght@300;400;500&family=Open+Sans:wght@400;600&display=swap" rel="stylesheet">
<style>
:root{
  --green:#6cc04a;
  --green-dark:#4f9e32;
  --ink:#333;
  --muted:#666;
  --dark:#262626;
  --darker:#1b1b1b;
  --light:#f3f3f3;
  --stone:#e9e7e2;
  --white:#fff;
}
*{box-sizing:border-box;margin:0;padding:0}
html,body{width:1200px;height:4891px;overflow:hidden}
body{font-family:"Open Sans",Arial,sans-serif;color:var(--ink);background:var(--white);position:relative}
section,header,footer{position:absolute;left:0;width:1200px;overflow:hidden}
.btn{display:inline-block;background:var(--green);color:var(--white);font-family:"Raleway",Arial,sans-serif;font-weight:500;font-size:19px;text-transform:uppercase;border-radius:30px;padding:0 34px;line-height:58px;text-decoration:none;white-space:nowrap}
.section-title{font-family:"Raleway",Arial,sans-serif;font-weight:400;text-transform:uppercase;font-size:44px;line-height:54px;color:var(--green);letter-spacing:1px}
.section-sub{font-family:"Raleway",Arial,sans-serif;font-size:20px;color:var(--ink)}
.photo{display:block}

/* hero */
.hero{top:0;height:650px;background:linear-gradient(180deg,#9fb3b4 0%,#c9cfc8 40%,#8d877c 75%,#5a5148 100%)}
.hero .photo{position:absolute;inset:0;background:linear-gradient(160deg,rgba(190,205,205,.7),rgba(120,110,95,.6))}
.nav-bar{position:absolute;top:0;left:0;width:1200px;height:150px}
.brand{position:absolute;left:78px;top:30px;display:flex;align-items:center;gap:12px}
.brand-dot{width:68px;height:68px;border-radius:50%;background:var(--dark);border:3px solid var(--green)}
.brand-name{font-family:"Raleway",Arial,sans-serif;font-size:44px;font-weight:400;color:var(--green)}
.top-phone{position:absolute;right:82px;top:14px;display:flex;align-items:center;gap:10px;color:var(--white);font-size:19px;font-weight:600}
.top-phone .ico{width:30px;height:30px;border-radius:50%;background:var(--green);display:flex;align-items:center;justify-content:center}
.main-nav{position:absolute;left:440px;top:58px;display:flex;gap:6px;list-style:none}
.main-nav a{display:block;color:var(--white);font-size:17px;font-weight:600;text-transform:uppercase;text-decoration:none;padding:0 18px;line-height:50px;border-radius:6px}
.main-nav .active a{background:var(--green)}
.hero-title{position:absolute;top:312px;left:0;width:1200px;text-align:center;font-family:"Oswald",Arial,sans-serif;font-weight:600;font-size:56px;line-height:68px;color:var(--white);text-transform:uppercase;text-shadow:0 2px 6px rgba(0,0,0,.4)}
.hero .btn{position:absolute;top:458px;left:477px}

/* welcome */
.welcome{top:650px;height:475px;text-align:center}
.welcome .section-title{margin-top:88px}
.welcome .section-sub{margin-top:2px;font-size:22px}
.welcome p{width:760px;margin:30px auto 0;font-size:15px;line-height:25px;color:var(--muted)}
.welcome .btn{margin-top:34px}

/* feature rows */
.feature{height:355px}
.feature h2{font-family:"Raleway",Arial,sans-serif;font-weight:400;text-transform:uppercase;font-size:38px;line-height:48px;color:var(--green)}
.feature p{font-size:15px;line-height:24px;margin-top:14px;width:620px}
.feature .btn{margin-top:24px;line-height:52px;font-size:18px}
.feature .text{position:absolute;top:70px}
.feature .ring{position:absolute;top:42px;width:272px;height:272px}
.feature .ring .photo{position:absolute;left:20px;top:20px;width:232px;height:232px;border-radius:50%;border:6px solid var(--white)}
.feature .ring svg{position:absolute;inset:0}
.feature-stone{background:linear-gradient(90deg,#dcd8d0,#eeebe5 60%,#d6d2c9);color:var(--ink)}
.feature-stone p{color:#555}
.feature-dark{background:linear-gradient(90deg,#2c2c2c,#3a3a3a 55%,#232323);color:var(--white)}
.feature-dark p{color:#ddd}
.feature-light{background:var(--white);color:var(--ink)}
.feature-light p{color:var(--muted)}
.r-left .ring{left:88px}
.r-left .text{left:430px}
.r-right .ring{left:828px}
.r-right .text{left:78px}

/* testimonial */
.testimonial{top:2543px;height:352px;background:linear-gradient(90deg,#2a2a2a,#3b3b3b,#2a2a2a);color:var(--white);text-align:center}
.testimonial .section-title{margin-top:50px;font-size:40px;line-height:50px}
.quote-mark{font-family:Georgia,serif;font-size:64px;line-height:50px;margin-top:10px;color:var(--green)}
.testimonial blockquote{width:900px;margin:8px auto 0;font-size:16px;line-height:26px;color:#e6e6e6}
.client{margin-top:18px;font-size:14px;font-weight:600;text-transform:uppercase;color:var(--green)}
.client:before{content:"";display:inline-block;width:40px;height:2px;background:var(--green);vertical-align:middle;margin-right:10px}
.avatar{position:absolute;top:2817px;left:536px;width:128px;height:128px;border-radius:50%;border:5px solid var(--white);box-shadow:0 0 0 4px var(--dark);background:linear-gradient(160deg,#7a5238,#c89a7e);z-index:2}

/* products */
.products{top:2895px;height:610px;text-align:center}
.products .section-title{margin-top:100px}
.product-grid{position:absolute;top:190px;left:82px;display:flex;gap:16px}
.product-card{width:247px;height:350px;background:var(--light)}
.product-card .photo{height:185px}
.product-card h3{font-family:"Raleway",Arial,sans-serif;font-weight:500;font-size:21px;margin-top:18px;color:var(--ink)}
.product-card p{font-size:14px;line-height:21px;color:var(--muted);width:210px;margin:10px auto 0}
.product-card .chev{margin-top:14px}

/* contact */
.contact{top:3505px;height:358px;background:linear-gradient(180deg,#2a2a2a,#1f1f1f);text-align:center;color:var(--white)}
.contact .section-title{margin-top:78px}
.contact .lead{font-family:"Raleway",Arial,sans-serif;font-size:21px;margin-top:4px}
.contact .call{font-size:16px;font-weight:600;margin-top:10px}
.contact-form{position:absolute;top:213px;left:112px;display:flex;gap:12px}
.contact-form .field{width:258px;height:50px;background:var(--white);border-radius:3px;color:var(--muted);font-size:14px;text-align:left;padding:0 12px;line-height:50px}
.contact-form .btn{line-height:50px;padding:0 44px;margin-left:4px}

/* gallery */
.gallery{top:3863px;height:782px;text-align:center}
.gallery .section-title{margin-top:82px}
.gallery .photo{position:absolute}
.gallery .btn{position:absolute;top:694px;left:520px}

/* footer */
.site-footer{top:4645px;height:246px;background:var(--darker);color:#bbb}
.foot-nav{position:absolute;top:43px;left:82px;display:flex;gap:14px;list-style:none}
.foot-nav a{color:#ccc;text-decoration:none;font-size:15px;display:block;padding:0 16px;line-height:38px;border-radius:20px}
.foot-nav .active a{border:2px solid var(--green);color:var(--white)}
.social{position:absolute;right:82px;top:42px;display:flex;gap:12px}
.social span{width:40px;height:40px;border-radius:50%;background:var(--green);display:block}
.foot-rule{position:absolute;top:106px;left:82px;width:1036px;height:1px;background:#333}
.foot-title{position:absolute;top:125px;left:82px;font-family:"Raleway",Arial,sans-serif;font-size:24px;color:var(--green)}
.foot-info{position:absolute;top:168px;left:82px;display:flex;gap:36px;font-size:13px;line-height:19px}
.foot-info .item{display:flex;align-items:center;gap:12px}
.foot-info .ico{width:36px;height:36px;border-radius:50%;border:2px solid var(--green);display:flex;align-items:center;justify-content:center;flex:none}
.copy{color:var(--green);font-weight:600}
.copy small{color:#bbb;font-weight:400;font-size:13px}
</style>
</head>
<body>

<header class="hero">
  <div class="photo" role="img" aria-label="Bright living room with large glass walls opening onto a terrace and garden"></div>
  <div class="nav-bar">
    <div class="brand"><span class="brand-dot"></span><span class="brand-name">Velmarix</span></div>
    <div class="top-phone"><span class="ico"><svg width="16" height="16" viewBox="0 0 24 24"><path fill="#fff" d="M6.6 10.8a15 15 0 0 0 6.6 6.6l2.2-2.2c.3-.3.7-.4 1-.2 1.1.4 2.3.6 3.6.6.6 0 1 .4 1 1V20c0 .6-.4 1-1 1A17 17 0 0 1 3 4c0-.6.4-1 1-1h3.5c.6 0 1 .4 1 1 0 1.2.2 2.4.6 3.6.1.3 0 .7-.2 1z"/></svg></span>416-555-0182</div>
    <ul class="main-nav">
      <li class="active"><a href="#">Home</a></li>
      <li><a href="#">About</a></li>
      <li><a href="#">Services</a></li>
      <li><a href="#">Products</a></li>
      <li><a href="#">Gallery</a></li>
      <li><a href="#">Contact</a></li>
    </ul>
  </div>
  <h1 class="hero-title">Specializing in motorized systems for<br>indoors and outdoors</h1>
  <a class="btn" href="#">Contact us now</a>
</header>

<section class="welcome">
  <h2 class="section-title">Welcome to Velmarix</h2>
  <div class="section-sub">Window Treatment Solution</div>
  <p>Custom high quality window treatments for homes, condos and buildings across Toronto and the GTA. Over 15 years of expertise, personal attention on every project, and top-of-the-line motorized and manual systems from leading makers such as Dimbrell.</p>
  <a class="btn" href="#">Know more</a>
</section>

<section class="feature feature-stone r-left" style="top:1125px">
  <div class="ring">
    <svg width="272" height="272" viewBox="0 0 272 272"><path d="M136 6a130 130 0 0 0 0 260" fill="none" stroke="#6cc04a" stroke-width="10"/></svg>
    <div class="photo" role="img" aria-label="Roller shades lowered over a glass wall" style="background:linear-gradient(160deg,#cfd8d6,#6c7a78)"></div>
  </div>
  <div class="text">
    <h2>Roller Shades</h2>
    <p>Our own locally made roller shades, sized to every window and motorized for quiet, precise control.</p>
    <a class="btn" href="#">Know more</a>
  </div>
</section>

<section class="feature feature-light r-right" style="top:1477px">
  <div class="ring">
    <svg width="272" height="272" viewBox="0 0 272 272"><path d="M136 6a130 130 0 0 1 0 260" fill="none" stroke="#6cc04a" stroke-width="10"/></svg>
    <div class="photo" role="img" aria-label="Outdoor bug screen on a covered patio" style="background:linear-gradient(160deg,#dfe6ea,#8a9aa3)"></div>
  </div>
  <div class="text">
    <h2>Outdoor Bug Screens</h2>
    <p>Retractable screens that keep the view open and the insects out, hidden away when not in use.</p>
    <a class="btn" href="#">Know more</a>
  </div>
</section>

<section class="feature feature-dark r-left" style="top:1832px">
  <div class="ring">
    <svg width="272" height="272" viewBox="0 0 272 272"><path d="M136 6a130 130 0 0 0 0 260" fill="none" stroke="#6cc04a" stroke-width="10"/></svg>
    <div class="photo" role="img" aria-label="Woven awning shading a window" style="background:linear-gradient(160deg,#c9a46a,#7a5c34)"></div>
  </div>
  <div class="text">
    <h2>Awnings</h2>
    <p>Motorized awnings that bring shade to terraces and windows with a single touch.</p>
    <a class="btn" href="#">Know more</a>
  </div>
</section>

<section class="feature feature-light r-right" style="top:2184px">
  <div class="ring">
    <svg width="272" height="272" viewBox="0 0 272 272"><path d="M136 6a130 130 0 0 1 0 260" fill="none" stroke="#6cc04a" stroke-width="10"/></svg>
    <div class="photo" role="img" aria-label="White drapery on an outdoor pavilion beside a lawn" style="background:linear-gradient(160deg,#e9ece6,#6f8a55)"></div>
  </div>
  <div class="text">
    <h2>Drapery</h2>
    <p>Tailored indoor and outdoor drapery in fine fabrics, finished by hand for a soft, elegant frame.</p>
    <a class="btn" href="#">Know more</a>
  </div>
</section>

<section class="testimonial">
  <h2 class="section-title">What our client say</h2>
  <div class="quote-mark">&ldquo;</div>
  <blockquote>"Lorem Ipsum is simply dummy text of the printing and typesetting industry. Lorem Ipsum has been the industry's standard dummy text ever since the 1500s."</blockquote>
  <div class="client">Client name</div>
</section>
<div class="avatar" role="img" aria-label="Client portrait"></div>

<section class="products">
  <h2 class="section-title">Our Product</h2>
  <div class="section-sub">What We Provide</div>
  <div class="product-grid">
    <div class="product-card">
      <div class="photo" role="img" aria-label="Roller shades in a glass sunroom" style="background:linear-gradient(160deg,#d7dedb,#7f8b86)"></div>
      <h3>Roller shades</h3>
      <p>Locally made, fully motorized.</p>
      <svg class="chev" width="16" height="12" viewBox="0 0 16 12"><path d="M2 2l6 6 6-6" fill="none" stroke="#6cc04a" stroke-width="2.5"/></svg>
    </div>
    <div class="product-card">
      <div class="photo" role="img" aria-label="Outdoor bug screens on a dining patio" style="background:linear-gradient(160deg,#9aa79a,#3f4a3d)"></div>
      <h3>Outdoor Bug Screens</h3>
      <p>Open views, no insects.</p>
      <svg class="chev" width="16" height="12" viewBox="0 0 16 12"><path d="M2 2l6 6 6-6" fill="none" stroke="#6cc04a" stroke-width="2.5"/></svg>
    </div>
    <div class="product-card">
      <div class="photo" role="img" aria-label="Awning with sheer curtains over a garden view" style="background:linear-gradient(160deg,#e8eaef,#8b93a8)"></div>
      <h3>Awnings</h3>
      <p>Shade at a single touch.</p>
      <svg class="chev" width="16" height="12" viewBox="0 0 16 12"><path d="M2 2l6 6 6-6" fill="none" stroke="#6cc04a" stroke-width="2.5"/></svg>
    </div>
    <div class="product-card">
      <div class="photo" role="img" aria-label="Outdoor pergola beside a large window" style="background:linear-gradient(160deg,#f1f1ee,#b4ab9c)"></div>
      <h3>Outdoor Pergolas</h3>
      <p>Living space, outdoors.</p>
      <svg class="chev" width="16" height="12" viewBox="0 0 16 12"><path d="M2 2l6 6 6-6" fill="none" stroke="#6cc04a" stroke-width="2.5"/></svg>
    </div>
  </div>
</section>

<section class="contact">
  <h2 class="section-title">Contact Us</h2>
  <div class="lead">Please fill email form and we will respond shortly</div>
  <div class="call">Call Us On 416-555-0182</div>
  <div class="contact-form">
    <div class="field">Name*</div>
    <div class="field">Email*</div>
    <div class="field">Subject*</div>
    <a class="btn" href="#">Submit</a>
  </div>
</section>

<section class="gallery">
  <h2 class="section-title">Our Gallery</h2>
  <div class="section-sub">Our Best Work</div>
  <div class="photo" role="img" aria-label="Glass roof over a terrace with sea view" style="left:82px;top:189px;width:563px;height:228px;background:linear-gradient(160deg,#b9d4e6,#5b7f96)"></div>
  <div class="photo" role="img" aria-label="Awning over a balcony" style="left:662px;top:189px;width:218px;height:228px;background:linear-gradient(160deg,#c9a57a,#6f8aa0)"></div>
  <div class="photo" role="img" aria-label="Shaded outdoor lounge" style="left:896px;top:189px;width:225px;height:228px;background:linear-gradient(160deg,#5c6a4d,#2f3528)"></div>
  <div class="photo" role="img" aria-label="Interior with tall windows" style="left:82px;top:427px;width:218px;height:228px;background:linear-gradient(160deg,#d2d6d4,#7a8480)"></div>
  <div class="photo" role="img" aria-label="Covered patio at night" style="left:313px;top:427px;width:225px;height:228px;background:linear-gradient(160deg,#d39a54,#3a2a1d)"></div>
  <div class="photo" role="img" aria-label="Glass screens on a modern terrace" style="left:554px;top:427px;width:567px;height:228px;background:linear-gradient(160deg,#e4e6e6,#8d9391)"></div>
  <a class="btn" href="#">View all</a>
</section>

<footer class="site-footer">
  <ul class="foot-nav">
    <li class="active"><a href="#">Home</a></li>
    <li><a href="#">About</a></li>
    <li><a href="#">Services</a></li>
    <li><a href="#">Product</a></li>
    <li><a href="#">Gallery</a></li>
    <li><a href="#">Contact</a></li>
  </ul>
  <div class="social"><span></span><span></span><span></span></div>
  <div class="foot-rule"></div>
  <div class="foot-title">Contact Us</div>
  <div class="foot-info">
    <div class="item"><span class="ico"><svg width="14" height="18" viewBox="0 0 14 18"><path d="M7 1a6 6 0 0 0-6 6c0 4.5 6 10 6 10s6-5.5 6-10a6 6 0 0 0-6-6zm0 8.2A2.2 2.2 0 1 1 7 4.8a2.2 2.2 0 0 1 0 4.4z" fill="#6cc04a"/></svg></span><span>27 Larkmoor Rd, Toronto,<br>ON, M4G 2K8</span></div>
    <div class="item"><span class="ico"><svg width="12" height="18" viewBox="0 0 12 18"><rect x="1" y="1" width="10" height="16" rx="2" fill="none" stroke="#6cc04a" stroke-width="1.6"/><circle cx="6" cy="14" r="1" fill="#6cc04a"/></svg></span><span>416-555-0182</span></div>
    <div class="item"><span class="ico"><svg width="18" height="18" viewBox="0 0 18 18"><circle cx="9" cy="9" r="7.5" fill="none" stroke="#6cc04a" stroke-width="1.6"/><path d="M1.5 9h15M9 1.5c-3 3.5-3 11.5 0 15M9 1.5c3 3.5 3 11.5 0 15" fill="none" stroke="#6cc04a" stroke-width="1.2"/></svg></span><span>www.velmarix.ca</span></div>
    <div class="copy">&copy;Velmarix Window Treatment<br>Solution <small>- 2016, All Rights Reserved</small></div>
  </div>
</footer>

</body>
</html>
```